The Marigold Venture WEBSITE DESIGN

Marigold is a not for profit working in international aid and development. The website needs to be lively not depressing,earthy rather than bling, have a dramatic impact over lightweight. It may be that a black and white with spot colour may be more impacting given the simplicity I want for the site. Marigold works in partnership with registered NGOs in Asia and Africa. At any one time it will have about five feature projects. The purpose is for people to be able to find out about the projects, the countries, the partner organisations, people's stories and then give people the opportunity to give their financial and volunteer support.

Target Market(s)

First World Donors
All ages but particularly 25 - 55

Industry/Entity Type

Human Rights

Number of Pages Required

5+ page

Font styles to use
Sans Serif

Requirements
Must have
• Simplicity
• Easy access to giving options
• Highlight stories both video and image + copy (sample in attachments)
• Lots of images over copy
Nice to have
• Interest
• Not boring
• May work in black and white with a spot colour or sepia look
Should not have
• Shiny new look
• Dont know how many pages or if it be coded or uncoded - makes no sense to me

```html
<!DOCTYPE html>
<html lang="en">
<head>
<meta charset="utf-8">
<title>Marigold project inc.</title>
<link href="https://fonts.googleapis.com/css2?family=Arimo:wght@400;700&family=Oswald:wght@300;400;600&display=swap" rel="stylesheet">
<style>
:root{
  --ink:#000;
  --panel:#0d0d0d;
  --white:#fff;
  --orange:#f6a91b;
  --green:#9bc31c;
  --teal:#4fc3b4;
  --light:#e5e2de;
  --grey:#8a8a8a;
  --mid:#5d5d5d;
  --text:#9b9b9b;
}
*{margin:0;padding:0;box-sizing:border-box}
html,body{width:786px;height:1200px;overflow:hidden;background:var(--ink)}
body{font-family:"Arimo",Arial,sans-serif;color:var(--white);position:relative}

.site-header{position:absolute;left:31px;top:0;width:729px;height:47px;display:flex;align-items:center;justify-content:space-between}
.brand{font-size:22px;font-weight:700;color:var(--white)}
.main-nav{display:flex;gap:0;font-size:12px;height:100%;align-items:center}
.main-nav a{color:var(--white);text-decoration:none;padding:10px 8px}
.main-nav a.active{background:var(--orange);color:var(--ink)}

.hero{position:absolute;left:31px;top:47px;width:729px;height:431px;background:var(--panel)}
.hero-photo{position:absolute;left:150px;top:0;width:579px;height:431px;background:radial-gradient(ellipse at 55% 35%,#d9d9d9 0%,#8c8c8c 40%,#3a3a3a 75%,#1a1a1a 100%)}
.action-tabs{position:absolute;left:0;top:0;width:184px;height:431px;display:flex;flex-direction:column}
.action-tab{height:143.6px;padding:24px 0 0 18px;clip-path:polygon(0 0,88% 0,100% 50%,88% 100%,0 100%);font-family:"Oswald",sans-serif}
.action-tab strong{display:block;font-size:36px;font-weight:400;line-height:1;letter-spacing:1px}
.action-tab span{display:block;font-size:13px;letter-spacing:2px;margin-top:6px}
.tab-donate{background:var(--orange)}
.tab-volunteer{background:var(--green)}
.tab-help{background:var(--teal)}
.mission{position:absolute;right:0;font-family:"Oswald",sans-serif;color:var(--white)}
.mission-line1{top:313px;width:372px;height:40px;background:var(--ink);font-size:26px;padding:2px 14px;letter-spacing:.5px}
.mission-line2{top:359px;width:288px;height:44px;background:#6b6b6b;font-size:28px;font-weight:300;padding:2px 16px}

.values{position:absolute;left:31px;top:498px;width:729px;height:242px;background:var(--light);display:flex;gap:14px;padding:14px 14px}
.value{flex:1;color:#333}
.value h2{font-size:17px;font-weight:400;margin-bottom:10px;color:#222}
.value-photo{height:84px;background:linear-gradient(90deg,#2a2a2a,#9a9a9a 50%,#444)}
.value p{font-size:8.5px;line-height:1.45;color:var(--grey);margin-top:8px;height:50px;overflow:hidden}
.btn{display:inline-block;font-size:8px;padding:3px 10px;text-decoration:none}
.value .btn{background:var(--ink);color:var(--white);float:right}

.goal{position:absolute;left:31px;top:760px;width:729px;height:120px;display:flex;align-items:center}
.goal h2{width:190px;text-align:center;font-size:22px;font-weight:400;line-height:1.5}
.goal-mark{font-family:"Oswald",sans-serif;font-size:60px;line-height:1;align-self:flex-start;margin-top:10px;width:40px}
.goal blockquote{flex:1;font-size:14.5px;line-height:1.45}

.news{position:absolute;left:31px;top:895px;width:729px;height:170px;background:#111;display:flex;padding:18px 14px;gap:18px}
.news-item{flex:1}
.news-date{font-size:27px;font-weight:400}
.news-date b{font-weight:700}
.news-title{font-size:9px;font-weight:700;margin:4px 0 6px}
.news-item p{font-size:8.5px;line-height:1.45;color:var(--mid);height:40px}
.news-item .btn{color:var(--ink);font-weight:700}
.c-orange{color:var(--orange)} .b-orange{background:var(--orange)}
.c-green{color:var(--green)} .b-green{background:var(--green)}
.c-teal{color:var(--teal)} .b-teal{background:var(--teal)}

.site-footer{position:absolute;left:31px;top:1082px;width:729px;height:118px;border-top:1px solid #333}
.footer-brand{position:absolute;left:0;top:16px;font-size:24px;font-weight:700}
.footer-nav{position:absolute;left:0;top:67px;font-size:10.5px;display:flex;gap:7px}
.footer-nav a{color:var(--white);text-decoration:none}
.social{position:absolute;right:0;top:40px;display:flex;gap:4px}
.social span{width:14px;height:14px;background:var(--teal);display:block}
.phone{position:absolute;right:0;top:60px;font-size:26px;color:var(--orange)}
</style>
</head>
<body>
<header class="site-header">
  <div class="brand">Marigold project inc.</div>
  <nav class="main-nav">
    <a class="active" href="#">Home</a><a href="#">About Marigold</a><a href="#">Introduction</a><a href="#">News</a><a href="#">Giving</a><a href="#">Contact</a>
  </nav>
</header>

<section class="hero">
  <div class="hero-photo" role="img" aria-label="Black and white photo of smiling children"></div>
  <div class="action-tabs">
    <a class="action-tab tab-donate"><strong>MAKE</strong><span>DONATIONS</span></a>
    <a class="action-tab tab-volunteer"><strong>JOIN</strong><span>VOLUNTEER</span></a>
    <a class="action-tab tab-help"><strong>HELP</strong><span>CHILDREN</span></a>
  </div>
  <div class="mission mission-line1">“OurMISSIONis toHELP</div>
  <div class="mission mission-line2">Those WhoNEEDit</div>
</section>

<section class="values">
  <article class="value">
    <h2>Capacity of People</h2>
    <div class="value-photo" role="img" aria-label="Black and white photos of young people"></div>
    <p>We believe that families and young people have the capacity to shape their own future and build stronger, lasting communities together with us.</p>
    <a class="btn" href="#">Read more</a>
  </article>
  <article class="value">
    <h2>Development Driven</h2>
    <div class="value-photo" role="img" aria-label="Black and white photo of a child"></div>
    <p>We believe that lasting change must be driven locally, led by partners who understand the needs and strengths of each village they serve.</p>
    <a class="btn" href="#">Read more</a>
  </article>
  <article class="value">
    <h2>Shared Responsibility</h2>
    <div class="value-photo" role="img" aria-label="Black and white photo of joined hands"></div>
    <p>We believe that responsibility rests with all partners of the project, working with integrity, openness and respect for every person we meet.</p>
    <a class="btn" href="#">Read more</a>
  </article>
</section>

<section class="goal">
  <h2>Overarching<br>Goal:</h2>
  <div class="goal-mark">“</div>
  <blockquote>To partner with Kivu Hope Alliance to establish 1000 women's Self Help Groups (SHGs) in the southern province of Rwanda.</blockquote>
</section>

<section class="news">
  <article class="news-item">
    <div class="news-date c-orange"><b>June 31</b>2011</div>
    <div class="news-title c-orange">New wells open in Huye</div>
    <p>Families in three villages now have clean water close to home this season.</p>
    <a class="btn b-orange" href="#">READ MORE</a>
  </article>
  <article class="news-item">
    <div class="news-date c-green"><b>June 29</b>2011</div>
    <div class="news-title c-green">Volunteers return from Kigali</div>
    <p>Our team shares stories and photos from two weeks of work in schools.</p>
    <a class="btn b-green" href="#">READ MORE</a>
  </article>
  <article class="news-item">
    <div class="news-date c-teal"><b>June 17</b>2011</div>
    <div class="news-title c-teal">Savings groups reach 400</div>
    <p>Women's groups keep growing as members save together and start small businesses.</p>
    <a class="btn b-teal" href="#">READ MORE</a>
  </article>
</section>

<footer class="site-footer">
  <div class="footer-brand">Marigold project inc.</div>
  <nav class="footer-nav">
    <a href="#">Home</a>|<a href="#">About Marigold</a>|<a href="#">Introduction</a>|<a href="#">News</a>|<a href="#">Giving</a>|<a href="#">Contact</a>
  </nav>
  <div class="social"><span></span><span></span></div>
  <div class="phone">+1 800 555 01 23</div>
</footer>
</body>
</html>
```